Business Card Design Project for Heron Lending

Hello there,

We are looking for a business card design for our new Heron Lending car financing company. We are looking for a business card that will include:

- An address
- Telephone number and extension
- Employee Name
- Employee Title
- Our logo and name clearly visible

We are including our logo with this writeup, we are looking to convey friendliness, trus and memorability. Colors and everything else is up to you.

Target Market(s)

18-34 year old males and females

Industry/Entity Type

Business

```html
<!DOCTYPE html>
<html lang="en">
<head>
<meta charset="utf-8">
<title>Heron Lending – Business Cards</title>
<link href="https://fonts.googleapis.com/css2?family=Gelasio:wght@400;500&display=swap" rel="stylesheet">
<style>
  :root {
    --page: #e9e9ea;
    --card: #ffffff;
    --navy: #1f2330;
    --accent: #5a7fc6;
    --brand: #2c3a78;
    --ink: #15161a;
    --divider: #b9bfd3;
  }
  * { margin: 0; padding: 0; box-sizing: border-box; }
  html, body {
    width: 1200px;
    height: 914px;
    overflow: hidden;
    background: var(--page);
    font-family: "Gelasio", Georgia, serif;
  }
  .sheet {
    position: relative;
    width: 1200px;
    height: 914px;
  }
  .card {
    position: absolute;
    left: 250px;
    width: 700px;
    height: 400px;
    background: var(--card);
    overflow: hidden;
    box-shadow: 0 4px 14px rgba(0,0,0,0.12);
  }
  .card--back { top: 40px; }
  .card--front { top: 474px; }
  .card__swoosh {
    position: absolute;
    inset: 0;
    width: 100%;
    height: 100%;
  }
  .brand {
    position: absolute;
    display: flex;
    align-items: center;
    gap: 14px;
    color: var(--brand);
    font-weight: 500;
  }
  .brand__dot {
    border-radius: 50%;
    background: var(--brand);
    flex: none;
  }
  .brand__text { display: flex; flex-direction: column; line-height: 1; }
  .brand__name { letter-spacing: 0.06em; }
  .brand__sub { letter-spacing: 0.55em; margin-top: 8px; }

  .card--back .brand { left: 50%; top: 120px; transform: translateX(-50%); }
  .card--back .brand__dot { width: 40px; height: 40px; }
  .card--back .brand__name { font-size: 58px; }
  .card--back .brand__sub { font-size: 20px; }

  .card--front .brand { left: 40px; top: 90px; }
  .card--front .brand__dot { width: 24px; height: 24px; }
  .card--front .brand__name { font-size: 36px; }
  .card--front .brand__sub { font-size: 13px; margin-top: 6px; }

  .card__divider {
    position: absolute;
    left: 300px;
    top: 30px;
    width: 2px;
    height: 190px;
    background: linear-gradient(var(--card), var(--divider), var(--card));
  }
  .contact {
    position: absolute;
    left: 300px;
    top: 110px;
    width: 390px;
    text-align: center;
    color: var(--ink);
  }
  .contact__name { font-size: 34px; color: var(--accent); font-weight: 500; line-height: 1.1; }
  .contact__title { font-size: 18px; margin-bottom: 18px; }
  .contact__line { font-size: 19px; line-height: 1.3; }
</style>
</head>
<body>
<main class="sheet">

  <section class="card card--back" aria-label="Card back">
    <svg class="card__swoosh" viewBox="0 0 700 400" preserveAspectRatio="none" aria-hidden="true">
      <path d="M0 262 C 240 246 500 272 700 322 L700 400 L0 400 Z" fill="var(--accent)"/>
      <path d="M0 274 C 240 260 500 288 700 340 L700 400 L0 400 Z" fill="var(--navy)"/>
    </svg>
    <div class="brand">
      <span class="brand__dot"></span>
      <span class="brand__text">
        <span class="brand__name">HERON</span>
        <span class="brand__sub">LENDING</span>
      </span>
    </div>
  </section>

  <section class="card card--front" aria-label="Card front">
    <svg class="card__swoosh" viewBox="0 0 700 400" preserveAspectRatio="none" aria-hidden="true">
      <path d="M0 218 C 260 214 520 300 700 400 L0 400 Z" fill="var(--accent)"/>
      <path d="M0 234 C 255 232 510 316 680 400 L0 400 Z" fill="var(--navy)"/>
    </svg>
    <div class="brand">
      <span class="brand__dot"></span>
      <span class="brand__text">
        <span class="brand__name">HERON</span>
        <span class="brand__sub">LENDING</span>
      </span>
    </div>
    <div class="card__divider"></div>
    <div class="contact">
      <p class="contact__name">Employee Name</p>
      <p class="contact__title">Project Manager</p>
      <p class="contact__line">+1 (555) 0142 736</p>
      <p class="contact__line">48 Alder St., Brookfield, NY 10031</p>
      <p class="contact__line">P.O. Box: 407129</p>
    </div>
  </section>

</main>
</body>
</html>
```